AnswerCraft Website Redesign

I'm looking to redesign our website AnswerCraft.com. The main goal is to give it a fresh design that is easy on the eyes and pushes the users to creating an account.

Our platform is very simple and we only do one thing, we use ai to generate response to customer and product reviews.

See attached file to see the pricing section style.

On the homepage just under the hero section, I would like to include the wording:
"Write replies to the reviews you get on sites like:" then show the logos like we have on our register page: https://app.answercraft.com/public/index.php

Target Market(s)

Business owners with brick and morter business or any business or product that gets online reviews

Industry/Entity Type

reputation management

Number of Pages Required

2 page

Requirements
Must have
• Home page and pricing page

```html
<!DOCTYPE html>
<html lang="en">
<head>
<meta charset="utf-8">
<title>AnswerCraft — Website Redesign</title>
<link href="https://fonts.googleapis.com/css2?family=Poppins:wght@400;500;600;700&family=Playfair+Display:wght@400&display=swap" rel="stylesheet">
<style>
:root{
  --stage:#0b5cf2;
  --navy:#0d1c54;
  --navy-deep:#0b1744;
  --blue:#1f44a8;
  --band:#2f4fae;
  --gold:#f2bd17;
  --amber:#ffab00;
  --cream:#fffaea;
  --cream-line:#f3e3a6;
  --ink:#2b2f45;
  --muted:#5b6177;
  --card-head:#eef0fa;
  --white:#ffffff;
}
*{box-sizing:border-box;margin:0;padding:0}
html,body{width:944px;height:1200px;overflow:hidden;background:var(--stage)}
body{font-family:"Poppins",sans-serif;color:var(--ink)}
.board{position:absolute;left:0;top:0;width:1708px;height:2172px;transform:scale(0.55269);transform-origin:0 0;background:var(--stage)}
.page{position:absolute;width:782px;overflow:hidden;background:var(--white)}
.page--home{left:47px;top:153px;height:2019px}
.page--pricing{left:880px;top:0;height:2080px}
.abs{position:absolute}
.serif{font-family:"Playfair Display",serif;font-weight:400}
.center{left:0;right:0;text-align:center}
.btn{position:absolute;display:flex;align-items:center;justify-content:center;font-size:7.5px;font-weight:600;letter-spacing:.5px;border-radius:3px}
.btn--navy{background:var(--blue);color:var(--white)}
.btn--cream{background:var(--cream);border:1px solid var(--cream-line);color:var(--navy)}
.btn--outline{border:1px solid var(--navy);color:var(--navy);background:var(--white)}
.btn span{font-weight:400;margin-left:3px}
.placeholder{position:absolute}

.nav{position:absolute;left:0;top:0;width:782px;height:43px;border-bottom:1px solid #eef0f5}
.logo{position:absolute;display:flex;align-items:center;gap:6px;font-weight:700;font-size:15px;color:var(--navy)}
.logo i{display:block;width:18px;height:18px;background:var(--blue);border-radius:3px}
.nav__links{position:absolute;left:307px;top:18px;display:flex;gap:15px;font-size:6.5px;color:var(--ink)}

.hero__kicker{left:72px;top:114px;font-size:24px;color:var(--gold)}
.hero__title{left:72px;top:140px;font-size:29px;line-height:31px;font-weight:700;color:var(--navy)}
.hero__title em{font-style:normal;color:#1a4ee6}
.hero__lead{left:72px;top:214px;font-size:10px;line-height:15px;color:var(--navy);font-weight:500;width:300px}

.band{position:absolute;left:0;top:375px;width:782px;height:112px;background:var(--band)}
.band__label{top:35px;font-size:7.5px;font-weight:600;letter-spacing:1px;color:var(--white)}
.band__brands{position:absolute;left:98px;right:95px;top:60px;display:flex;justify-content:space-between;font-size:17px;font-weight:500;color:var(--white)}

.benefits{position:absolute;left:0;top:487px;width:782px;height:440px;background:linear-gradient(#ffffff,#eef1f8)}
.benefits__kicker{top:40px;font-size:11px;font-weight:700;color:var(--navy)}
.benefits__lead{top:60px;font-size:10px;line-height:14px;color:var(--navy)}
.benefit{position:absolute;top:108px;width:150px;height:240px;background:var(--white);border-radius:4px;box-shadow:0 2px 8px rgba(20,40,100,.08);text-align:center}
.benefit .placeholder{left:3px;top:3px;width:144px;height:120px;border-radius:2px}
.benefit h3{position:absolute;top:136px;left:0;right:0;font-size:12px;line-height:15px;font-weight:600;color:var(--navy)}
.benefit hr{position:absolute;top:173px;left:59px;width:32px;border:0;border-top:1px solid #2a54d0}
.benefit p{position:absolute;top:186px;left:14px;right:14px;font-size:6px;line-height:9.5px;color:var(--muted)}

.how__kicker{top:970px;font-size:22px;color:var(--gold)}
.how__title{top:994px;font-size:27px;line-height:31px;font-weight:700;color:var(--navy)}
.steps-card{position:absolute;left:103px;width:577px;height:342px;background:var(--cream);border-radius:10px}
.step{position:absolute;width:150px;text-align:center;color:var(--navy)}
.step .placeholder{left:50px;width:50px;height:34px;border-radius:6px}
.step b{display:block;font-family:"Playfair Display",serif;font-weight:400;font-size:10px}
.step small{display:block;font-size:7px;line-height:9px}
.steps-card__rule{position:absolute;left:34px;width:508px;border-top:1px solid var(--cream-line)}
.steps-card__active{position:absolute;left:220px;width:136px;height:2px;background:var(--amber)}
.feature__kicker{position:absolute;left:34px;font-size:10px;color:#2a54d0}
.feature__title{position:absolute;left:34px;font-size:22px;line-height:24px;font-weight:700;color:var(--navy)}
.feature__text{position:absolute;left:34px;font-size:7.5px;line-height:10.5px;color:var(--ink)}

.pricing{position:absolute;left:0;width:782px;height:697px;background:linear-gradient(180deg,#0a153f 0%,#13276e 60%,#1d3d9f 100%);overflow:hidden}
.pricing__ring{position:absolute;left:191px;top:130px;width:400px;height:400px;border-radius:50%;border:1px solid rgba(255,255,255,.06)}
.pricing__kicker{top:43px;font-size:24px;color:var(--gold)}
.pricing__title{top:75px;font-size:28px;line-height:31px;font-weight:700;color:var(--white)}
.pricing__bar{position:absolute;left:361px;top:186px;width:60px;height:3px;background:var(--gold)}
.pricing__lead{top:200px;font-size:9px;color:#e5e9f8}
.plan{position:absolute;top:238px;width:290px;height:404px;background:var(--white);border-radius:8px;overflow:hidden}
.plan__head{position:absolute;left:4px;right:4px;top:4px;height:94px;background:var(--card-head);border-radius:6px 6px 0 0;text-align:center}
.plan__stars{position:absolute;left:0;right:0;top:14px;display:flex;justify-content:center;gap:2px}
.plan__name{position:absolute;left:0;right:0;top:48px;font-family:"Playfair Display",serif;font-size:14px;color:var(--navy)}
.plan__sub{position:absolute;left:0;right:0;top:70px;font-size:7px;color:var(--ink)}
.plan__price{position:absolute;left:0;right:0;text-align:center;font-size:12px;font-weight:600;color:var(--navy)}
.plan__price span{font-size:7.5px;font-weight:400}
.slider{position:absolute;left:36px;top:137px;width:219px}
.slider__ends{display:flex;justify-content:space-between;font-size:9px;font-weight:600;color:var(--navy)}
.slider__track{position:relative;margin-top:6px;height:5px;border-radius:3px;background:#dfe4f4}
.slider__fill{position:absolute;left:0;top:0;width:54px;height:5px;border-radius:3px;background:var(--blue)}
.slider__knob{position:absolute;left:48px;top:-3px;width:11px;height:11px;border-radius:50%;background:var(--white);border:2px solid var(--blue)}
.slider__note{margin-top:9px;text-align:center;font-size:7px;color:var(--ink)}
.plan__cta{position:absolute;left:36px;width:219px;height:30px;border-radius:2px;display:flex;align-items:center;justify-content:center;font-size:10px;font-weight:600;color:var(--white)}
.plan__cta--amber{background:var(--amber)}
.plan__cta--navy{background:var(--blue)}
.plan__list{position:absolute;left:30px;right:22px;list-style:none}
.plan__list li{display:flex;align-items:center;gap:8px;height:28.5px;border-bottom:1px solid #edf0f6;font-size:8px;color:var(--ink)}
.plan__list svg{flex:none}

.faq__kicker{top:1080px;font-size:24px;color:var(--gold)}
.faq__title{top:1103px;font-size:29px;font-weight:700;color:var(--navy)}
.faq-item{position:absolute;width:290px;border-bottom:1px solid #f1d98a;font-size:7px;font-weight:500;color:var(--navy)}
.faq-item q{quotes:none;display:block;padding-right:30px;line-height:9.5px}
.faq-item__sign{position:absolute;right:12px;top:-2px;font-size:11px;color:#2a54d0;font-weight:600}
.faq-item p{margin-top:9px;font-size:6px;line-height:9px;font-weight:400;color:var(--muted);padding-bottom:16px}

.cta{position:absolute;left:0;top:1600px;width:782px;height:245px;background:var(--amber)}
.cta__title{top:50px;font-size:35px;line-height:40px;font-weight:700;color:var(--white)}
.cta__lead{top:135px;font-size:12px;color:var(--white)}

.footer{position:absolute;left:0;top:1845px;width:782px;height:235px;background:var(--navy-deep)}
.footer__col{position:absolute;top:58px;color:var(--white)}
.footer__col h4{font-family:"Playfair Display",serif;font-weight:400;font-size:12px;margin-bottom:8px}
.footer__col li{list-style:none;font-size:6.5px;line-height:19px;color:#d7dcf0}
.footer__social{position:absolute;left:153px;top:107px;display:flex;gap:8px}
.footer__social i{display:block;width:20px;height:20px;border-radius:50%;border:1px solid rgba(255,255,255,.6)}
.footer__rule{position:absolute;left:137px;right:137px;top:200px;border-top:1px solid rgba(255,255,255,.1)}
.footer__copy{top:215px;font-size:6.5px;color:#b9c0dc}
.footer__copy b{font-weight:600;color:var(--white)}
</style>
</head>
<body>
<div class="board">

  <section class="page page--home">
    <header class="nav">
      <div class="logo" style="left:72px;top:11px"><i></i>AnswerCraft</div>
      <nav class="nav__links"><span>Why Reply?</span><span>How It Works</span><span>Pricing</span><span>Blog</span></nav>
      <div class="btn btn--outline" style="left:592px;top:12px;width:52px;height:21px;font-size:6.5px">SIGN IN</div>
      <div class="btn btn--navy" style="left:649px;top:12px;width:61px;height:21px;font-size:6.5px">TRY FREE</div>
    </header>

    <div class="placeholder" role="img" aria-label="3D illustration of a woman typing on a laptop at a desk in front of a blue circle"
         style="left:440px;top:50px;width:340px;height:352px;background:radial-gradient(circle at 150px 170px,#1f5ef0 0 95px,#eef3ff 96px 150px,transparent 151px)"></div>

    <div class="abs serif hero__kicker">Write Personalized</div>
    <h1 class="abs hero__title">Responses To Reviews<br>In 10 Seconds! <em>(No Joke)</em></h1>
    <p class="abs hero__lead">GET STARTED TODAY WITH ONE FREE REPLY TO YOUR REVIEW. NO CREDIT CARD REQUIRED.</p>
    <div class="btn btn--navy" style="left:72px;top:260px;width:87px;height:31px">GET <span>STARTED</span></div>
    <div class="btn btn--cream" style="left:163px;top:260px;width:88px;height:31px">LEARN <span>MORE</span></div>

    <div class="band">
      <div class="abs center band__label">WRITE REPLIES TO THE REVIEWS YOU GET ON SITES LIKE</div>
      <div class="band__brands"><span>Searchfox</span><span>Munchly</span><span>Makerie</span><span>StarVerdict</span><span>Shopwell</span><span>Wayfarer</span><span>Nestly</span></div>
    </div>

    <section class="benefits">
      <svg class="abs" style="left:653px;top:0" width="110" height="57"><polygon points="0,0 110,0 62,57" fill="#2f4fae"/></svg>
      <div class="abs center benefits__kicker">ITS' SIMPLE,</div>
      <p class="abs center benefits__lead">Our tool writes replies and responses to the reviews your<br>customers leave. Doesn't matter if it's 1 or 5 stars.</p>

      <article class="benefit" style="left:73px">
        <div class="placeholder" role="img" aria-label="Photo of hands on a laptop showing an SEO diagram" style="background:linear-gradient(135deg,#c9b39a,#6c5a4c)"></div>
        <h3>Improved<br>SEO</h3><hr>
        <p>Searchfox loves seeing you leave a reply to your reviews and will give you a boost in their search results and local SEO.</p>
      </article>
      <article class="benefit" style="left:236px">
        <div class="placeholder" role="img" aria-label="Photo of two colleagues shaking hands in an office" style="background:linear-gradient(135deg,#b7aa9c,#4e5468)"></div>
        <h3>Build Customer<br>Trust</h3><hr>
        <p>Customers want to know there are humans behind your companies product or service. Show them you value their time.</p>
      </article>
      <article class="benefit" style="left:399px">
        <div class="placeholder" role="img" aria-label="Photo of a hand touching a row of glowing rating stars" style="background:linear-gradient(135deg,#c5c9cf,#7c818a)"></div>
        <h3>Increase Customer<br>Loyalty</h3><hr>
        <p>Taking the time to reply to a review shows your customers you care about them and their business. Show them some love!</p>
      </article>
      <article class="benefit" style="left:561px">
        <div class="placeholder" role="img" aria-label="Photo of a smiling couple reviewing a document together" style="background:linear-gradient(135deg,#8e9cb3,#d89a4c)"></div>
        <h3>Convert New<br>Customers</h3><hr>
        <p>FACT: Potential customers read reviews before making a decision. Give a good first impression with personalized replies.</p>
      </article>

      <div class="btn btn--navy" style="left:339px;top:370px;width:104px;height:30px">GET <span>STARTED</span></div>
    </section>

    <div class="abs center serif how__kicker">How it work</div>
    <h2 class="abs center how__title">Just three easy step to get<br>started with AnswerCraft</h2>

    <div class="steps-card" style="top:1083px">
      <div class="step" style="left:31px;top:40px"><div class="placeholder" role="img" aria-label="Sign-up form icon" style="top:0;background:linear-gradient(#f2f5ff,#dfe5fb)"></div><div style="height:44px"></div><b>STEP #1</b><small>Create An Account</small></div>
      <div class="step" style="left:213px;top:40px"><div class="placeholder" role="img" aria-label="Small star review icon" style="top:0;background:linear-gradient(#f2f5ff,#dfe5fb)"></div><div style="height:44px"></div><b>STEP #2</b><small>Copy &amp; Paste The Review</small></div>
      <div class="step" style="left:385px;top:40px"><div class="placeholder" role="img" aria-label="Stopwatch icon" style="top:0;background:linear-gradient(#fff0c7,#f4d27a)"></div><div style="height:44px"></div><b>STEP #3</b><small>Personalized Response<br>In Seconds</small></div>
      <div class="steps-card__rule" style="top:125px"></div>
      <div class="steps-card__active" style="top:124px"></div>
      <div class="feature__kicker serif" style="top:152px">STEP #2</div>
      <div class="feature__title" style="top:167px">We make it<br>way too simple!</div>
      <p class="feature__text" style="top:228px">Just Copy The Customer Review And Paste<br>It Into Your Account Dashboard</p>
      <div class="btn btn--cream" style="left:34px;top:268px;width:87px;height:29px">LEARN <span>MORE</span></div>
      <div class="placeholder" role="img" aria-label="Isometric illustration of people placing stars onto a large rating card" style="left:290px;top:150px;width:250px;height:165px;background:radial-gradient(ellipse at 60% 50%,#e8ecf8 0 55%,transparent 56%)"></div>
    </div>

    <section class="pricing" style="top:1477px">
      <div class="pricing__ring"></div>
      <div class="abs center serif pricing__kicker">Plans &amp; Pricing</div>
      <h2 class="abs center pricing__title">Never worry about having to come<br>up with a unique response to each<br>review ever again!</h2>
      <div class="pricing__bar"></div>
      <p class="abs center pricing__lead">If your business, product or service receives reviews, this tool will save you hundreds of hours.</p>

      <article class="plan" style="left:94px">
        <div class="plan__head">
          <div class="plan__stars"><svg width="30" height="28" viewBox="0 0 24 23"><polygon points="12,0 15,8 24,8.6 17,14 19.4,23 12,18 4.6,23 7,14 0,8.6 9,8" fill="#f6c02a"/></svg></div>
          <div class="plan__name">Monthly Subscriptions</div>
          <div class="plan__sub">Perfect For Getting Started For One Business/product</div>
        </div>
        <div class="plan__price" style="top:114px">Starts At $9.99 <span>/ Month</span></div>
        <div class="slider"><div class="slider__ends"><span>50K</span><span>700K+</span></div><div class="slider__track"><div class="slider__fill"></div><div class="slider__knob"></div></div><div class="slider__note">5000 word credits</div></div>
        <div class="plan__cta plan__cta--amber" style="top:193px">Start For Free</div>
        <ul class="plan__list" style="top:239px">
          <li><svg width="14" height="11"><polyline points="1,5 5,9 13,1" fill="none" stroke="#1f5ef0" stroke-width="2.4"/></svg>Personalized responses</li>
          <li><svg width="14" height="11"><polyline points="1,5 5,9 13,1" fill="none" stroke="#1f5ef0" stroke-width="2.4"/></svg>30+ Languages</li>
          <li><svg width="14" height="11"><polyline points="1,5 5,9 13,1" fill="none" stroke="#1f5ef0" stroke-width="2.4"/></svg>Auto-Save</li>
          <li><svg width="14" height="11"><polyline points="1,5 5,9 13,1" fill="none" stroke="#1f5ef0" stroke-width="2.4"/></svg>Revision History</li>
          <li style="border:0"><svg width="14" height="11"><polyline points="1,5 5,9 13,1" fill="none" stroke="#1f5ef0" stroke-width="2.4"/></svg>Assign members usage limits</li>
        </ul>
      </article>
      <article class="plan" style="left:399px">
        <div class="plan__head">
          <div class="plan__stars"><svg width="30" height="28" viewBox="0 0 24 23"><polygon points="12,0 15,8 24,8.6 17,14 19.4,23 12,18 4.6,23 7,14 0,8.6 9,8" fill="#f6c02a"/></svg><svg width="30" height="28" viewBox="0 0 24 23"><polygon points="12,0 15,8 24,8.6 17,14 19.4,23 12,18 4.6,23 7,14 0,8.6 9,8" fill="#f6c02a"/></svg></div>
          <div class="plan__name">Agency Subscriptions</div>
          <div class="plan__sub">Perfect For Multiple Clients/products Per Month</div>
        </div>
        <div class="plan__price" style="top:128px">Starting at $75.00 <span>/ month</span></div>
        <div class="plan__cta plan__cta--navy" style="top:169px">Start For Free</div>
        <ul class="plan__list" style="top:212px">
          <li><svg width="14" height="11"><polyline points="1,5 5,9 13,1" fill="none" stroke="#1f5ef0" stroke-width="2.4"/></svg>Everything in the Startup plan</li>
          <li><svg width="14" height="11"><polyline points="1,5 5,9 13,1" fill="none" stroke="#1f5ef0" stroke-width="2.4"/></svg>Dedicated Account Manager</li>
          <li><svg width="14" height="11"><polyline points="1,5 5,9 13,1" fill="none" stroke="#1f5ef0" stroke-width="2.4"/></svg>Onboarding &amp; Training</li>
          <li style="border:0"><svg width="14" height="11"><polyline points="1,5 5,9 13,1" fill="none" stroke="#1f5ef0" stroke-width="2.4"/></svg>Unlimited Integrations</li>
        </ul>
      </article>
    </section>
  </section>

  <section class="page page--pricing">
    <div class="steps-card" style="top:-60px">
      <div class="step" style="left:31px;top:80px"><b>STEP #1</b><small>Create An Account</small></div>
      <div class="step" style="left:213px;top:80px"><b>STEP #2</b><small>Copy &amp; Paste The Review</small></div>
      <div class="step" style="left:385px;top:80px"><b>STEP #3</b><small>Personalized Response<br>In Seconds</small></div>
      <div class="steps-card__rule" style="top:126px"></div>
      <div class="steps-card__active" style="top:125px"></div>
      <div class="feature__kicker serif" style="top:156px">STEP #2</div>
      <div class="feature__title" style="top:172px">We make it<br>way too simple!</div>
      <p class="feature__text" style="top:232px">Just Copy The Customer Review And Paste<br>It Into Your Account Dashboard</p>
      <div class="btn btn--cream" style="left:34px;top:267px;width:87px;height:31px">LEARN <span>MORE</span></div>
      <div class="placeholder" role="img" aria-label="Isometric illustration of people placing stars onto a large rating card" style="left:287px;top:150px;width:250px;height:165px;background:radial-gradient(ellipse at 60% 50%,#e8ecf8 0 55%,transparent 56%)"></div>
    </div>

    <section class="pricing" style="top:335px">
      <div class="pricing__ring"></div>
      <div class="abs center serif pricing__kicker">Plans &amp; Pricing</div>
      <h2 class="abs center pricing__title">Never worry about having to come<br>up with a unique response to each<br>review ever again!</h2>
      <div class="pricing__bar"></div>
      <p class="abs center pricing__lead">If your business, product or service receives reviews, this tool will save you hundreds of hours.</p>

      <article class="plan" style="left:93px">
        <div class="plan__head">
          <div class="plan__stars"><svg width="30" height="28" viewBox="0 0 24 23"><polygon points="12,0 15,8 24,8.6 17,14 19.4,23 12,18 4.6,23 7,14 0,8.6 9,8" fill="#f6c02a"/></svg></div>
          <div class="plan__name">Monthly Subscriptions</div>
          <div class="plan__sub">Perfect For Getting Started For One Business/product</div>
        </div>
        <div class="plan__price" style="top:114px">Starts At $9.99 <span>/ Month</span></div>
        <div class="slider"><div class="slider__ends"><span>50K</span><span>700K+</span></div><div class="slider__track"><div class="slider__fill"></div><div class="slider__knob"></div></div><div class="slider__note">5000 word credits</div></div>
        <div class="plan__cta plan__cta--amber" style="top:193px">Start For Free</div>
        <ul class="plan__list" style="top:239px">
          <li><svg width="14" height="11"><polyline points="1,5 5,9 13,1" fill="none" stroke="#1f5ef0" stroke-width="2.4"/></svg>Personalized responses</li>
          <li><svg width="14" height="11"><polyline points="1,5 5,9 13,1" fill="none" stroke="#1f5ef0" stroke-width="2.4"/></svg>30+ Languages</li>
          <li><svg width="14" height="11"><polyline points="1,5 5,9 13,1" fill="none" stroke="#1f5ef0" stroke-width="2.4"/></svg>Auto-Save</li>
          <li><svg width="14" height="11"><polyline points="1,5 5,9 13,1" fill="none" stroke="#1f5ef0" stroke-width="2.4"/></svg>Revision History</li>
          <li style="border:0"><svg width="14" height="11"><polyline points="1,5 5,9 13,1" fill="none" stroke="#1f5ef0" stroke-width="2.4"/></svg>Assign members usage limits</li>
        </ul>
      </article>
      <article class="plan" style="left:398px">
        <div class="plan__head">
          <div class="plan__stars"><svg width="30" height="28" viewBox="0 0 24 23"><polygon points="12,0 15,8 24,8.6 17,14 19.4,23 12,18 4.6,23 7,14 0,8.6 9,8" fill="#f6c02a"/></svg><svg width="30" height="28" viewBox="0 0 24 23"><polygon points="12,0 15,8 24,8.6 17,14 19.4,23 12,18 4.6,23 7,14 0,8.6 9,8" fill="#f6c02a"/></svg></div>
          <div class="plan__name">Agency Subscriptions</div>
          <div class="plan__sub">Perfect For Multiple Clients/products Per Month</div>
        </div>
        <div class="plan__price" style="top:128px">Starting at $75.00 <span>/ month</span></div>
        <div class="plan__cta plan__cta--navy" style="top:169px">Start For Free</div>
        <ul class="plan__list" style="top:212px">
          <li><svg width="14" height="11"><polyline points="1,5 5,9 13,1" fill="none" stroke="#1f5ef0" stroke-width="2.4"/></svg>Everything in the Startup plan</li>
          <li><svg width="14" height="11"><polyline points="1,5 5,9 13,1" fill="none" stroke="#1f5ef0" stroke-width="2.4"/></svg>Dedicated Account Manager</li>
          <li><svg width="14" height="11"><polyline points="1,5 5,9 13,1" fill="none" stroke="#1f5ef0" stroke-width="2.4"/></svg>Onboarding &amp; Training</li>
          <li style="border:0"><svg width="14" height="11"><polyline points="1,5 5,9 13,1" fill="none" stroke="#1f5ef0" stroke-width="2.4"/></svg>Unlimited Integrations</li>
        </ul>
      </article>
    </section>

    <svg class="abs" style="left:45px;top:1032px" width="84" height="58"><polygon points="0,0 84,0 25,58" fill="#1d3d9f"/></svg>

    <div class="abs center serif faq__kicker">Faq's</div>
    <h2 class="abs center faq__title">Frequetnly asked questions</h2>

    <div class="faq-item" style="left:72px;top:1193px;height:25px"><q>Why Is It Important To Respond To Searchfox Reviews?</q><span class="faq-item__sign">+</span></div>
    <div class="faq-item" style="left:420px;top:1193px;height:25px"><q>Why is it important to respond to negative reviews?</q><span class="faq-item__sign">+</span></div>
    <div class="faq-item" style="left:72px;top:1250px"><q>How can I trust someone who doesn't work at my business to reply to reviews on my behalf?</q><span class="faq-item__sign">−</span>
      <p>Building trust with a third-party can be challenging, but the rewards of having someone knowledgeable in this field could make all the difference when it comes to growing your business.</p></div>
    <div class="faq-item" style="left:420px;top:1250px;height:25px"><q>Which Online Review Sites Does AnswerCraft.com Support?</q><span class="faq-item__sign">+</span></div>
    <div class="abs" style="left:692px;top:1303px;font-size:11px;font-weight:600;color:#2a54d0">+</div>

    <div class="placeholder" role="img" aria-label="Photo of three young friends smiling at a phone with floating rating, like and follower badges"
         style="left:50px;top:1340px;width:630px;height:260px;background:linear-gradient(180deg,#ffffff 0%,#d9dde6 45%,#8a7a72 100%)"></div>

    <section class="cta">
      <h2 class="abs center cta__title">Ready to give<br>AnswerCraft a try?</h2>
      <p class="abs center serif cta__lead">Get started today with one FREE Reply to your Review. No credit card required.</p>
      <div class="btn btn--navy" style="left:338px;top:168px;width:104px;height:31px;box-shadow:0 3px 8px rgba(0,0,0,.15)">TRY FOR <span>FREE</span></div>
    </section>

    <footer class="footer">
      <div class="logo" style="left:137px;top:68px;color:var(--white);font-size:18px"><i style="width:24px;height:24px;background:transparent;border:2px solid var(--white)"></i>AnswerCraft</div>
      <div class="footer__social"><i></i><i></i><i></i></div>
      <div class="footer__col" style="left:329px"><h4>Sitelinks</h4><ul><li>Why Reply?</li><li>How It Works</li><li>Pricing</li><li>Blog</li></ul></div>
      <div class="footer__col" style="left:449px"><h4>Links</h4><ul><li>Blog</li><li>Privacy Policy</li><li>Contact</li><li>Sitemap</li></ul></div>
      <div class="footer__col" style="left:568px"><h4>Members</h4></div>
      <div class="btn btn--navy" style="left:566px;top:86px;width:80px;height:24px;border-radius:12px;background:#1f5ef0">Log in</div>
      <div class="btn" style="left:566px;top:116px;width:80px;height:24px;border-radius:12px;border:1px solid var(--white);color:var(--white)">Try Free</div>
      <div class="footer__rule"></div>
      <div class="abs center footer__copy">©2023 <b>AnswerCraft</b>, all rights reserved.</div>
    </footer>
    <svg class="abs" style="left:655px;top:1845px" width="80" height="56"><polygon points="0,0 80,0 55,56" fill="#ffab00"/></svg>
  </section>

</div>
</body>
</html>
```